Lumen Fitness Personal Training Business

I need a business card design with a logo for my personal training company. I'd like the colors to be a vibrant green and black. I'd like the logo to incorporate an anvil (or something similar). I train hardcore competitive athletes as well as soccer moms trying to get and/or stay in shape. I need a logo that will not pigeon hole me in one category or the other, but at the same time not be too intimidating to soccer moms, but will not be off putting to the more hardcore trainees. The design should be attention grabbing and aesthetic.
Target Market(s)
Hardcore athletes as well as average people just trying to get/stay in shape.
Industry/Entity Type
Training

```html
<!DOCTYPE html>
<html lang="en">
<head>
<meta charset="utf-8">
<title>Lumen Fitness – Business Card</title>
<link rel="stylesheet" href="https://fonts.googleapis.com/css2?family=Raleway:wght@400;500;600;700&display=swap">
<style>
  :root {
    --stage: #0c0c0d;
    --stage-edge: #050505;
    --card: #35363b;
    --card-shadow: rgba(0, 0, 0, 0.6);
    --green-deep: #1ea84b;
    --green-bright: #5cbf3f;
    --text-light: #e4e4e6;
    --text-muted: #a9aaae;
    --divider: #4b4c52;
  }
  * { box-sizing: border-box; margin: 0; padding: 0; }
  html, body {
    width: 1200px;
    height: 900px;
    overflow: hidden;
  }
  body {
    position: relative;
    background: radial-gradient(ellipse at center, var(--stage) 0%, var(--stage-edge) 100%);
    font-family: "Raleway", Arial, sans-serif;
  }
  .card {
    position: absolute;
    width: 478px;
    height: 278px;
    background: var(--card);
    border-radius: 14px;
    box-shadow: 0 8px 24px var(--card-shadow);
  }
  .card--front { left: 116px; top: 297px; }
  .card--back  { left: 632px; top: 299px; }

  .front-brand {
    position: absolute;
    left: 28px;
    top: 82px;
    width: 190px;
    font-weight: 700;
    font-size: 34px;
    line-height: 1.1;
    color: var(--green-deep);
  }

  .contact {
    position: absolute;
    left: 231px;
    top: 70px;
    color: var(--text-light);
  }
  .contact__name {
    font-size: 21px;
    font-weight: 500;
    color: var(--green-deep);
    line-height: 1.2;
  }
  .contact__name .surname { color: var(--green-bright); }
  .contact__role {
    font-size: 14px;
    color: var(--text-muted);
    margin-top: 1px;
    margin-left: 1px;
  }
  .contact__lines {
    margin-top: 17px;
    margin-left: 3px;
    font-size: 14.5px;
    line-height: 18px;
  }
  .contact__lines .label { color: var(--green-deep); }
  .contact__address {
    margin-top: 13px;
    margin-left: 3px;
    font-size: 14.5px;
    line-height: 18px;
  }

  .back-mark {
    position: absolute;
    left: 104px;
    top: 102px;
    width: 56px;
    height: 56px;
    border-radius: 50%;
    background: var(--green-deep);
  }
  .back-divider {
    position: absolute;
    left: 216px;
    top: 79px;
    width: 1px;
    height: 110px;
    background: var(--divider);
  }
  .back-brand {
    position: absolute;
    left: 238px;
    top: 90px;
    font-weight: 700;
    font-size: 34px;
    line-height: 1.1;
    color: var(--green-deep);
  }
</style>
</head>
<body>
  <section class="card card--front" aria-label="Business card front">
    <div class="front-brand">Lumen<br>Fitness</div>
    <div class="contact">
      <p class="contact__name">Daniel <span class="surname">Carter</span></p>
      <p class="contact__role">Managing Director</p>
      <div class="contact__lines">
        <p><span class="label">e:</span> hello@lumenfit.com</p>
        <p><span class="label">t:</span> 044-321 654 987</p>
      </div>
      <p class="contact__address">Unit 12, Forge Street 7841,<br>Millbrook, Westland 40217</p>
    </div>
  </section>

  <section class="card card--back" aria-label="Business card back">
    <span class="back-mark" aria-hidden="true"></span>
    <span class="back-divider" aria-hidden="true"></span>
    <div class="back-brand">Lumen<br>Fitness</div>
  </section>
</body>
</html>
```